Company Website for Varnoth Signal, an open source data analytics company focused on relationship and li

I need a company/brand website for our new startup, Varnoth Signal LLC. We are a company focused on using life pattern analysis techniques, looking at relationships and how relationships, attributes, and activity cluster to infer aggregate information about individuals and groups. Our focus is on improving the digital advertising market.

We have a company logo which I will upload shortly.

Target Market(s)

Digital Advertising

Number of Pages Required

3 page

Font styles to use
Sans Serif

Requirements
Must have
• An main page, about us, contact page.
Nice to have
• Varnoth Signal relies on state of the art analytics applied to a the digital marketing space. While it is heavy in science, we also understand the art of influence. The website should have a scientific edge but also a flair that illustrates our focus on applying the hard science and analytics to influencing the behavior of people.

```html
<!DOCTYPE html>
<html lang="en">
<head>
<meta charset="utf-8">
<title>Varnoth Signal — Digital Marketing Analysis and Influence</title>
<link rel="stylesheet" href="https://fonts.googleapis.com/css2?family=Montserrat:wght@400;500;600;700&display=swap">
<style>
:root{
  --blue:#1f6fc0;
  --blue-bright:#2a86d8;
  --blue-band:#1a6bc2;
  --ink:#ffffff;
  --muted:#c9ccd1;
  --hero:#16191d;
  --band:#2a2a2a;
  --subbar:#222222;
  --body:#1f1f1f;
  --footer:#262626;
  --bottom:#1e1e1e;
  --line:#3a3a3a;
}
*{box-sizing:border-box;margin:0;padding:0}
html,body{width:741px;height:1200px;overflow:hidden;background:var(--body)}
body{font-family:"Montserrat",Arial,sans-serif;color:var(--ink);position:relative}
.page{position:relative;width:741px;height:1200px}

/* hero */
.hero{position:absolute;left:0;top:0;width:741px;height:403px;
  background:radial-gradient(ellipse at 60% 30%,#1c3a4a 0%,#15222b 40%,var(--hero) 80%)}
.hero-art{position:absolute;inset:0}
.brand{position:absolute;left:72px;top:14px;display:flex;align-items:center;gap:6px;
  font-weight:700;font-size:13px;color:var(--blue-bright);letter-spacing:.5px}
.brand-dot{width:10px;height:10px;border-radius:50%;background:#f5a623}
.nav{position:absolute;top:22px;left:558px;display:flex;align-items:center;gap:15px;font-size:8px;font-weight:500}
.nav a{color:var(--ink);text-decoration:none}
.nav .active{color:var(--blue-bright);border-bottom:1px solid var(--blue-bright);padding-bottom:3px}
.nav-icons{display:flex;gap:4px;margin-left:-3px}
.nav-icon{width:12px;height:12px;border-radius:50%;display:flex;align-items:center;justify-content:center}
.nav-icon.cart{background:var(--blue-bright)}
.nav-icon.search{background:#555}
.hero-title{position:absolute;left:72px;top:163px;font-size:29px;font-weight:700;line-height:39px;letter-spacing:.3px}
.btn-products{position:absolute;left:74px;top:246px;width:108px;height:25px;background:var(--blue);
  font-size:9px;font-weight:700;letter-spacing:1px;display:flex;align-items:center;justify-content:center}
.btn-products::after{content:"";position:absolute;left:0;bottom:-8px;border-left:10px solid var(--blue);border-bottom:8px solid transparent}

/* why band */
.why{position:absolute;top:403px;left:0;width:741px;height:64px;background:var(--band);
  display:flex;align-items:center;justify-content:center;font-size:24px;font-weight:500;letter-spacing:1px}
.subbar{position:absolute;top:467px;left:0;width:741px;height:32px;background:var(--subbar);
  border-bottom:1px solid var(--line)}
.subbar span{position:absolute;left:68px;top:0;height:32px;border-left:1px solid var(--line);padding-left:6px;
  display:flex;align-items:center;font-size:7px;font-weight:600}

/* features */
.features{position:absolute;top:499px;left:0;width:741px;height:283px;background:var(--body)}
.pattern-visual{position:absolute;left:69px;top:33px;width:293px;height:100px;
  background:radial-gradient(circle at 15% 60%,#f1d3cf 0,#fbf2f1 22%,transparent 30%),
  radial-gradient(circle at 50% 50%,#d5e6e3 0,#f4f8f8 22%,transparent 30%),
  radial-gradient(circle at 85% 40%,#d4dcec 0,#f3f5fa 22%,transparent 30%),#ffffff}
.feature-title{position:absolute;left:69px;top:146px;font-size:18px;font-weight:500;letter-spacing:.4px}
.feature-text{position:absolute;left:70px;top:172px;width:295px;font-size:6px;line-height:12px;color:var(--muted)}
.point{position:absolute;left:377px;width:300px}
.point-num{position:absolute;left:0;top:0;width:36px;height:36px;border-radius:50%;background:var(--blue);
  display:flex;align-items:center;justify-content:center;font-size:17px;font-weight:400}
.point-title{position:absolute;left:52px;top:3px;font-size:7px;font-weight:500;color:var(--blue-bright);white-space:nowrap}
.point-text{position:absolute;left:52px;top:17px;width:250px;font-size:6px;line-height:14.5px;color:var(--muted)}

/* services band */
.services{position:absolute;top:782px;left:0;width:741px;height:281px;
  background:linear-gradient(135deg,#1a62b4 0%,#1d74cc 45%,#1a66ba 100%)}
.services-map{position:absolute;inset:0;
  background:radial-gradient(ellipse at 55% 40%,rgba(120,180,240,.35) 0%,transparent 55%)}
.tile{position:absolute;top:79px;width:120px;height:120px;border:1px solid rgba(255,255,255,.8);
  display:flex;align-items:center;justify-content:center}
.tile.featured{background:rgba(45,110,180,.85)}
.tile.featured::before{content:"";position:absolute;inset:3px;border:1px solid rgba(255,255,255,.7)}
.tile-caption{font-size:11.5px;font-weight:500;letter-spacing:1px;text-align:center;line-height:17.5px}
.tile-label{position:absolute;top:211px;width:70px;height:24px;border:1px solid #fff;
  display:flex;align-items:center;justify-content:center;font-size:7.5px;font-weight:500;letter-spacing:.8px}

/* footer */
.footer{position:absolute;top:1063px;left:0;width:741px;height:109px;background:var(--footer)}
.social{position:absolute;left:578px;top:53px;display:flex;gap:5px}
.social span{width:18px;height:18px;border-radius:50%;border:1px solid #777;display:block}
.email{position:absolute;left:578px;top:78px;width:89px;height:17px;border:1px solid #666;border-radius:9px;
  font-size:6px;color:#888;display:flex;align-items:center;justify-content:space-between;padding:0 7px 0 9px}
.to-top{position:absolute;top:1172px;left:0;width:741px;height:28px;background:var(--bottom);
  border-top:1px solid var(--line);display:flex;align-items:center;justify-content:center}
</style>
</head>
<body>
<div class="page">

  <header class="hero">
    <div class="hero-art" role="img" aria-label="Dark circuit-board backdrop with glowing blue and teal squares"></div>
    <div class="brand"><span class="brand-dot"></span>Varnoth Signal</div>
    <nav class="nav">
      <a class="active">Home</a>
      <a>Contact</a>
      <div class="nav-icons">
        <span class="nav-icon cart"><svg width="6" height="6" viewBox="0 0 10 10"><path d="M0 1h2l1.5 5h5L10 2.5H3" fill="none" stroke="#fff" stroke-width="1.4"/><circle cx="4" cy="8.5" r="1" fill="#fff"/><circle cx="8" cy="8.5" r="1" fill="#fff"/></svg></span>
        <span class="nav-icon search"><svg width="6" height="6" viewBox="0 0 10 10"><circle cx="4" cy="4" r="3" fill="none" stroke="#fff" stroke-width="1.5"/><path d="M6.2 6.2L9.5 9.5" stroke="#fff" stroke-width="1.5"/></svg></span>
      </div>
    </nav>
    <h1 class="hero-title">A NEW AGE IN DIGITAL MARKETING<br>ANALYSIS AND INFLUENCE</h1>
    <div class="btn-products">OUR PRODUCTS</div>
  </header>

  <section class="why">WHY WE ARE DIFFERENT</section>
  <div class="subbar"><span>MUCH MORE THAN CONTENT</span></div>

  <section class="features">
    <div class="pattern-visual" role="img" aria-label="Network diagram of red, teal and navy people clusters linked by thin lines"></div>
    <h2 class="feature-title">LIFE PATTERN ANALYSIS</h2>
    <p class="feature-text">Full spectrum digital information analysis provides a more complete picture of online activity, paths of influence, and audience insights resulting in more effective precision action.</p>

    <div class="point" style="top:32px">
      <div class="point-num">1</div>
      <div class="point-title">MEASURES OF EFFECT</div>
      <p class="point-text">More sophisticated measurements of online activity provides a more complete picture of campaign performance.</p>
    </div>
    <div class="point" style="top:115px">
      <div class="point-num">2</div>
      <div class="point-title">INFERRED INFORMATION</div>
      <p class="point-text">Analysis of clusters of online information provides information not reliant only on explicitly listed content.</p>
    </div>
    <div class="point" style="top:193px">
      <div class="point-num">3</div>
      <div class="point-title">PERCEPTION MANAGEMENT</div>
      <p class="point-text">Real-time, accurate brand, audience, and influencer analysis provides opportunity to capitalize on trends and more effectively manage brand perception.</p>
    </div>
  </section>

  <section class="services">
    <div class="services-map" role="img" aria-label="Faint blue world map and data charts backdrop"></div>

    <div class="tile featured" style="left:89px">
      <div class="tile-caption" style="position:relative">ENRICH YOUR<br>OWN<br>CUSTOMER<br>DATA SET</div>
      <svg style="position:absolute;left:96px;top:96px" width="22" height="26" viewBox="0 0 22 26"><path d="M1 1v20l5-5 4 8 3-1.5-4-8h7z" fill="#fff" stroke="#222" stroke-width="1.2"/></svg>
    </div>
    <div class="tile" style="left:233px">
      <svg width="56" height="44" viewBox="0 0 56 44" fill="#fff"><rect x="2" y="24" width="7" height="14"/><rect x="11" y="18" width="7" height="20"/><rect x="20" y="12" width="7" height="26"/><path d="M2 20L14 12l8 4 14-12" fill="none" stroke="#fff" stroke-width="2"/><path d="M32 2h6v6" fill="none" stroke="#fff" stroke-width="2"/><circle cx="38" cy="26" r="10" fill="none" stroke="#fff" stroke-width="3"/><path d="M45 33l8 8" stroke="#fff" stroke-width="4"/><rect x="0" y="39" width="34" height="3"/></svg>
    </div>
    <div class="tile" style="left:383px">
      <svg width="50" height="40" viewBox="0 0 50 40"><path d="M14 32H11a9 9 0 010-18 12 12 0 0123-3 9 9 0 016 17" fill="none" stroke="#fff" stroke-width="3"/><rect x="23" y="17" width="4" height="14" fill="#fff"/><rect x="23" y="34" width="4" height="4" fill="#fff"/></svg>
    </div>
    <div class="tile" style="left:532px">
      <svg width="48" height="44" viewBox="0 0 48 44" fill="#fff"><path d="M10 10a18 12 0 0128-2" fill="none" stroke="#fff" stroke-width="2"/><path d="M10 4v7h7" fill="none" stroke="#fff" stroke-width="2"/><path d="M38 34a18 12 0 01-28 2" fill="none" stroke="#fff" stroke-width="2"/><path d="M38 40v-7h-7" fill="none" stroke="#fff" stroke-width="2"/><circle cx="15" cy="18" r="4"/><rect x="9" y="23" width="12" height="6" rx="3"/><circle cx="33" cy="18" r="4"/><rect x="27" y="23" width="12" height="6" rx="3"/></svg>
    </div>

    <div class="tile-label" style="left:115px">DATA</div>
    <div class="tile-label" style="left:258px">ANANLYTICS</div>
    <div class="tile-label" style="left:408px">RISK</div>
    <div class="tile-label" style="left:557px">INFLUENCE</div>
  </section>

  <footer class="footer">
    <div class="social"><span></span><span></span><span></span><span></span></div>
    <div class="email">Your email<svg width="7" height="6" viewBox="0 0 7 6"><path d="M0 3h6M4 1l2 2-2 2" fill="none" stroke="#aaa" stroke-width="1"/></svg></div>
  </footer>
  <div class="to-top"><svg width="12" height="8" viewBox="0 0 12 8"><path d="M1 7l5-5 5 5" fill="none" stroke="#fff" stroke-width="2"/></svg></div>

</div>
</body>
</html>
```